Business Card for Inovative Flexible Packaging Company

Create a business card that is both simple and stricking at the same time.
Preferably only one color (orange) or two colors (black and orange).
Information to print:
Lumtrex, Lda
[T] 22 418 6095
[M] 91 362 7148
[F] 22 418 6037
[@] lumtrex.geral@mailvora.com
SEDE & ARMAZÉM
Rua Das Figueiras do Monte, 317
Valmorim
4415-238 Valmorim - VN Ribeira
PORTUGAL
Reason: A lot of the ideas are obvious. I want something different. Inovative. dare to do something eye catching with style.
Target Market(s)
Business Consumers. Packaging Designers.
Industry/Entity Type
Business
Look and feel
Each slider illustrates characteristics of the customer's brand and the style your logo design should communicate.

```html
<!DOCTYPE html>
<html lang="pt">
<head>
<meta charset="utf-8">
<title>Lumtrex business card</title>
<link rel="stylesheet" href="https://fonts.googleapis.com/css2?family=Poppins:wght@500&family=Tinos&display=swap">
<style>
  :root {
    --orange: #ff4a12;
    --orange-pale: #fde3d6;
    --ink: #111111;
    --card-black: #070708;
    --card-white: #ffffff;
    --board: #eeeef0;
  }
  * { margin: 0; padding: 0; box-sizing: border-box; }
  html, body { width: 1200px; height: 900px; overflow: hidden; background: var(--board); }
  .board { position: relative; width: 1200px; height: 900px; }

  .card {
    position: absolute; top: 176px; width: 540px; height: 313px;
    box-shadow: 6px 6px 8px rgba(0,0,0,0.45);
    overflow: hidden;
  }
  .card--front { left: 52px; background: var(--card-black); }
  .card--back { left: 632px; background: var(--card-white); }

  .brand { position: absolute; display: flex; align-items: center; font-family: "Poppins", sans-serif; font-weight: 500; color: var(--orange); }
  .brand__square { background: var(--orange); flex: none; }
  .brand__words { display: flex; flex-direction: column; }
  .brand__name { line-height: 1; letter-spacing: -0.5px; }
  .brand__tagline { letter-spacing: 0.3em; line-height: 1; white-space: nowrap; }

  .card--front .brand { left: 116px; top: 108px; gap: 12px; }
  .card--front .brand__square { width: 74px; height: 74px; }
  .card--front .brand__name { font-size: 50px; }
  .card--front .brand__tagline { font-size: 10px; margin-top: 6px; }

  .card--back .brand { left: 22px; top: 20px; gap: 10px; }
  .card--back .brand__square { width: 56px; height: 56px; }
  .card--back .brand__name { font-size: 38px; }
  .card--back .brand__tagline { font-size: 8px; margin-top: 4px; }

  .back-accent { position: absolute; left: 262px; top: 30px; width: 210px; height: 210px; background: var(--orange-pale); opacity: 0.6; }

  .details { position: absolute; font-family: "Tinos", serif; color: var(--ink); }
  .details__company { left: 43px; top: 132px; font-size: 19px; }
  .contact-list { left: 43px; top: 164px; list-style: none; font-size: 15.5px; line-height: 23px; }
  .contact-list li { display: flex; align-items: center; gap: 6px; }
  .contact-list svg { width: 12px; height: 12px; fill: var(--orange); flex: none; }
  .address { left: 276px; top: 154px; font-size: 15.5px; line-height: 20.5px; font-style: normal; }

  .stripes { position: absolute; left: 0; bottom: 0; width: 540px; height: 20px; }

  .brand--board { left: 826px; top: 783px; gap: 14px; }
  .brand--board .brand__square { width: 86px; height: 86px; }
  .brand--board .brand__name { font-size: 62px; }
  .brand--board .brand__tagline { font-size: 11.5px; margin-top: 6px; }
</style>
</head>
<body>
<main class="board">

  <section class="card card--front" aria-label="Card front">
    <div class="brand">
      <span class="brand__square"></span>
      <span class="brand__words">
        <span class="brand__name">lumtrex</span>
        <span class="brand__tagline">SMART FLEXIBLE WRAPS</span>
      </span>
    </div>
  </section>

  <section class="card card--back" aria-label="Card back">
    <div class="back-accent" role="img" aria-label="Soft brand colour field"></div>
    <div class="brand">
      <span class="brand__square"></span>
      <span class="brand__words">
        <span class="brand__name">lumtrex</span>
        <span class="brand__tagline">SMART FLEXIBLE WRAPS</span>
      </span>
    </div>

    <p class="details details__company">Lumtrex, Lda</p>
    <ul class="details contact-list">
      <li><svg viewBox="0 0 12 12" aria-hidden="true"><path d="M2.5 0.5l2 2.5-1.2 1.3c.7 1.6 2 2.9 3.5 3.6l1.3-1.2 2.4 2-1.3 2.3C4.8 10.6 1.3 7 .5 2.1z"/></svg>22 418 6095</li>
      <li><svg viewBox="0 0 12 12" aria-hidden="true"><path d="M3 0h6v12H3zM4 1.5v7.5h4V1.5z"/></svg>91 362 7148</li>
      <li><svg viewBox="0 0 12 12" aria-hidden="true"><path d="M3 0h5v4H3zM0 4h12v8H0zM2 6v1.5h2V6zm3 0v1.5h2V6zm3 0v1.5h2V6zM2 9v1.5h2V9zm3 0v1.5h2V9zm3 0v1.5h2V9z"/></svg>22 418 6037</li>
      <li><svg viewBox="0 0 12 12" aria-hidden="true"><path d="M0 2h12v1L6 7 0 3zM0 4.3l6 4 6-4V10H0z"/></svg>lumtrex.geral@mailvora.com</li>
    </ul>
    <address class="details address">
      SEDE &amp; ARMAZÉM<br>
      Rua Das Figueiras do Monte, 317<br>
      Valmorim<br>
      4415-238 Valmorim - VN Ribeira<br>
      PORTUGAL
    </address>

    <svg class="stripes" viewBox="0 0 540 20" preserveAspectRatio="none" aria-hidden="true">
      <polygon points="195,4 540,4 540,8 190,8" fill="var(--orange)"/>
      <polygon points="175,12 540,12 540,20 163,20" fill="var(--ink)"/>
    </svg>
  </section>

  <div class="brand brand--board">
    <span class="brand__square"></span>
    <span class="brand__words">
      <span class="brand__name">lumtrex</span>
      <span class="brand__tagline">SMART FLEXIBLE WRAPS</span>
    </span>
  </div>

</main>
</body>
</html>
```